Unique Realty Niche needs a web design

Starting Note: Please do not use the colors from the logo on quickhousebarnowl.net which is their current website. This logo will eventually change but it is what they have now.

This website is a realty website that caters to individuals who want to rent out their homes (investors) and those who want to rent a home (Tenants). We provide no credit check to rent a home from a investor at a higher cost for the tenant to balance risk. Good renters with bad credit are able to rent or buy a house from investors who are registered in our system.

Target Market(s)

Home Owners trying to rent out their homes, and people looking to rent.

Industry/Entity Type

House

Requirements
Must have
• Main Navigation links: Home - Our Story - tenant - owner - contact us

A log in form somewhere on the page.

Key themes in the site are as follows: The site needs to be clean and professional looking i.e. no grunge. I provided some color palettes below, these are not set in stone and if you know of a good palette(s) our client is very open to all suggestions. The main navigation needs to stay on top but other on page navigations could go on left (preferably) On the left or the right will be featured listings for some homes. It will be between 3 to 5 listings showing at one time. (Please see quickhousebarnowl.net for example)

Example Color Palettes:
http://hueplank.example.org/#themeID/1634353
http://hueplank.example.org/#themeID/166988
http://hueplank.example.org/#themeID/1638382
http://hueplank.example.org/#themeID/1677863

Example Websites That Client Likes:
NOTE: Very Flexible, no need to duplicate these below.
http://www.fernlotgroupvx.net/
http://www.tqbgrove.net/
http://www.wubalestewards.net/index.php?pr=Home_Page

Nice to have
• It would be nice to have short easy to read paragraphs accompanied by a photo so scanning is easy on the site. Then in later pages we will have more text when there is more detail needed. We know you wont come up with the content but concept would be nice.

```html
<!DOCTYPE html>
<html lang="en">
<head>
<meta charset="utf-8">
<title>Quick House Barn Owl</title>
<link href="https://fonts.googleapis.com/css2?family=Arimo:wght@400;700&display=swap" rel="stylesheet">
<style>
:root{
  --ink:#111;
  --text:#333;
  --accent:#e0330e;
  --card:#3a3a3a;
  --nav:#050505;
  --line:#cfcfcf;
  --panel:#fff;
}
*{box-sizing:border-box;margin:0;padding:0}
html,body{width:900px;height:1200px;overflow:hidden}
body{position:relative;font-family:"Arimo",Arial,sans-serif;color:var(--text);
  background:linear-gradient(180deg,#f4f2f1 0,#ebe8e6 480px,#f7f6f5 1200px)}
.abs{position:absolute}
.topbar{left:0;top:0;width:900px;height:5px;background:#333}
.brand{left:24px;top:22px;display:flex;align-items:center;gap:12px}
.brand-mark{width:72px;height:72px;border-radius:50%;background:#d9d4cf}
.brand-name{font-size:22px;font-weight:700;color:#4a3f3a;letter-spacing:.3px}
.login{left:520px;top:30px;width:362px}
.login-row{display:flex;gap:6px;align-items:center}
.login-input{width:120px;height:20px;border:1px solid #aaa;background:#fff;font-size:10px;color:#999;display:flex;align-items:center;padding-left:5px}
.login-btn{width:64px;height:20px;border-radius:3px;background:linear-gradient(#555,#2d2d2d);color:#fff;font-size:11px;display:flex;align-items:center;justify-content:center}
.account{margin-top:9px;font-size:11px;color:var(--ink);display:flex;gap:6px;justify-content:flex-end;padding-right:30px}
.account .reg{color:var(--accent);text-decoration:underline}
.nav{left:18px;top:96px;width:864px;height:36px;background:var(--nav);display:flex}
.nav a{flex:1;color:#fff;font-size:14px;text-decoration:none;display:flex;align-items:center;justify-content:center;border-right:1px solid #333}
.nav a:last-child{border-right:0}
.hero{left:28px;top:132px;width:854px;height:323px;background:var(--panel);box-shadow:0 14px 12px -8px rgba(0,0,0,.35)}
.hero-photo{left:0;top:8px;width:572px;height:313px;background:linear-gradient(180deg,#c9d6e2 0,#bfb4a0 35%,#8c8576 60%,#4f7a2e 85%,#3d6a22 100%)}
.hero-caption{left:0;bottom:0;width:100%;height:36px;background:rgba(40,70,20,.75);color:#fff;font-size:11px;display:flex;align-items:center;padding-left:90px}
.search-title{left:609px;top:26px;color:var(--accent);font-size:17px;font-weight:700}
.lbl{font-size:11px;color:var(--ink)}
.field{height:20px;border:1px solid #aaa;background:#fff}
.sel::after{content:"";position:absolute;right:0;top:0;width:14px;height:18px;border-left:1px solid #ccc;background:linear-gradient(#f4f4f4,#ddd)}
.sel::before{content:"";position:absolute;right:4px;top:7px;border:3px solid transparent;border-top:4px solid #333;z-index:1}
.to{font-size:11px;color:var(--ink)}
.search-btn{left:647px;top:252px;width:118px;height:25px;border-radius:3px;background:linear-gradient(#555,#2d2d2d);color:#fff;font-size:11px;display:flex;align-items:center;justify-content:center}
.pager{left:256px;top:467px;width:100px;height:18px;border:1px solid #bbb;border-radius:9px;background:#fafafa;display:flex;align-items:center;justify-content:center;gap:4px}
.pager i{width:10px;height:10px;border-radius:50%;background:#333;display:block}
.pager i.on{background:var(--accent)}
.pager b{font-size:10px;font-weight:400;color:#333;margin:0 3px}
.section-title{font-size:18px;font-weight:700;color:#222}
.rule{height:1px;background:var(--line)}
.card{top:541px;width:212px;height:258px;background:var(--card);padding:6px 5px 0}
.card.active{background:var(--accent)}
.card-photo{width:100%;height:183px;background:linear-gradient(180deg,#9fb9d0 0,#c9c2b6 40%,#8e6a55 55%,#6b8a3d 80%,#8a8a7c 100%)}
.card-addr{color:#fff;font-size:16px;font-weight:700;text-align:center;line-height:20px;margin-top:9px}
.more{position:absolute;right:0;bottom:0;width:49px;height:18px;background:#111;color:#aaa;font-size:11px;display:flex;align-items:center;justify-content:center}
.listing{left:28px;width:420px}
.thumb{left:0;top:0;width:145px;height:94px;border:4px solid #fff;box-shadow:0 0 3px rgba(0,0,0,.3);background:linear-gradient(180deg,#7fa8d6 0,#9c8c78 50%,#6d8f45 75%,#9a9a92 100%)}
.thumb-link{left:13px;top:102px;font-size:11px;color:var(--accent)}
.blurb{left:158px;top:2px;width:270px;font-size:11px;line-height:16px;color:var(--ink)}
.specs{left:158px;top:46px;font-size:11px;line-height:16px;color:var(--ink);display:grid;grid-template-columns:99px 160px}
.scroll{left:468px;top:862px;width:8px;height:276px;background:#ddd;border-radius:4px}
.scroll-thumb{left:0;top:28px;width:8px;height:58px;background:var(--accent);border-radius:4px}
.video{left:541px;top:859px;width:321px;height:210px;background:#000}
.replay{left:110px;top:78px;display:flex;align-items:center;gap:8px;color:#fff;font-size:19px}
.replay span{width:32px;height:26px;border-radius:4px;background:linear-gradient(#eee,#999)}
.controls{left:0;bottom:0;width:100%;height:29px;background:linear-gradient(#444,#1c1c1c);display:flex;align-items:center;padding:0 10px;gap:12px;color:#fff;font-size:12px}
.progress{width:112px;height:8px;background:#c1121b;border-radius:4px;position:relative;margin-left:10px}
.progress::after{content:"";position:absolute;right:-6px;top:-3px;width:14px;height:14px;border-radius:50%;background:#eee}
.investors{left:556px;top:1080px;display:flex;align-items:center;gap:12px;font-size:13px;font-weight:700;color:#222}
.doc{width:32px;height:38px;background:#e7e7e7;border:1px solid #bbb;position:relative}
.doc::after{content:"";position:absolute;left:4px;bottom:6px;width:22px;height:10px;background:#c8150f}
.investors small{font-size:11px;font-weight:400;color:#888;margin-left:-8px}
.footer-links{left:0;top:1161px;width:900px;text-align:center;font-size:11px;color:#444}
.copyright{left:0;top:1181px;width:900px;text-align:center;font-size:11px;color:#444}
</style>
</head>
<body>
<div class="abs topbar"></div>

<header>
  <div class="abs brand">
    <div class="brand-mark"></div>
    <div class="brand-name">QUICK HOUSE BARN OWL</div>
  </div>
  <form class="abs login" aria-label="Log in">
    <div class="login-row">
      <div class="login-input">Username</div>
      <div class="login-input">Password</div>
      <div class="login-btn">Log in</div>
    </div>
    <div class="account"><span>new user ?</span><span class="reg">Register</span><span>Sign in</span><span>Help</span></div>
  </form>
  <nav class="abs nav">
    <a href="#">Home</a>
    <a href="#">Our Story</a>
    <a href="#">Tenant</a>
    <a href="#">Owner</a>
    <a href="#">Contact us</a>
  </nav>
</header>

<section class="abs hero">
  <div class="abs hero-photo" role="img" aria-label="Two-storey stucco and brick family home with a green front lawn">
    <div class="abs hero-caption">Lorem Ipsum has been the industry's standard dummytext ever since.</div>
  </div>
  <h2 class="abs search-title">FIND YOUR PROPERTY</h2>
  <span class="abs lbl" style="left:607px;top:67px">Price per month</span>
  <div class="abs field" style="left:607px;top:85px;width:90px"></div>
  <span class="abs to" style="left:702px;top:89px">to</span>
  <div class="abs field" style="left:715px;top:85px;width:90px"></div>
  <span class="abs lbl" style="left:607px;top:110px">Location</span>
  <div class="abs field sel" style="left:607px;top:129px;width:200px"></div>
  <span class="abs lbl" style="left:607px;top:153px">min bedrooms</span>
  <span class="abs lbl" style="left:717px;top:153px">property type</span>
  <div class="abs field sel" style="left:607px;top:172px;width:90px"></div>
  <div class="abs field sel" style="left:717px;top:172px;width:90px"></div>
  <span class="abs lbl" style="left:607px;top:195px">availability</span>
  <span class="abs lbl" style="left:717px;top:195px">furnished</span>
  <div class="abs field sel" style="left:607px;top:214px;width:90px"></div>
  <div class="abs field sel" style="left:717px;top:214px;width:90px"></div>
  <div class="abs search-btn">Search</div>
</section>

<div class="abs pager"><b>‹</b><i></i><i></i><i class="on"></i><i></i><b>›</b></div>

<div class="abs rule" style="left:18px;top:498px;width:864px"></div>
<h2 class="abs section-title" style="left:33px;top:506px">Featured Listings</h2>
<div class="abs rule" style="left:18px;top:534px;width:864px"></div>

<article class="abs card active" style="left:23px">
  <div class="card-photo" role="img" aria-label="Single-storey brick ranch home with a front lawn"></div>
  <p class="card-addr">2174 Wrenfield Drive<br>Dallas, TX 75229</p><span class="more">more</span>
</article>
<article class="abs card" style="left:238px">
  <div class="card-photo" role="img" aria-label="Brick house behind tall autumn trees"></div>
  <p class="card-addr">3318 Larkmoor Court<br>Arlington,TX 76016</p><span class="more">more</span>
</article>
<article class="abs card" style="left:452px">
  <div class="card-photo" role="img" aria-label="Red brick home with a two-car garage"></div>
  <p class="card-addr">5902 Pebblecrest Drive<br>Mesquite, TX 75181</p><span class="more">more</span>
</article>
<article class="abs card" style="left:666px">
  <div class="card-photo" role="img" aria-label="Two-storey siding and brick home with a garage"></div>
  <p class="card-addr">7415 Oakhollow Lane<br>Plano, TX 75024</p><span class="more">more</span>
</article>

<div class="abs rule" style="left:18px;top:814px;width:864px"></div>
<h2 class="abs section-title" style="left:33px;top:821px">Preforming each property as a unique one!</h2>
<h2 class="abs section-title" style="left:540px;top:821px">Why Us?</h2>
<div class="abs rule" style="left:18px;top:849px;width:864px"></div>

<div class="abs listing" style="top:874px">
  <div class="abs thumb" role="img" aria-label="Single-storey brick home"></div>
  <span class="abs thumb-link">click to view more image</span>
  <p class="abs blurb">Lorem Ipsum has been the industry's standard dummy text ever since.</p>
  <div class="abs specs"><span><b>Bedrooms</b> : 3</span><span><b>Lot size</b> : 3</span><span><b>Bathrooms</b>: 3</span><span><b>Prperty type</b>: Single Family</span><span><b>Sqft</b>: 2.102</span><span><b>Year built</b>: 2010</span></div>
</div>
<div class="abs rule" style="left:28px;top:999px;width:420px"></div>
<div class="abs listing" style="top:1009px">
  <div class="abs thumb" role="img" aria-label="Single-storey home with a garage and trees"></div>
  <span class="abs thumb-link">click to view more image</span>
  <p class="abs blurb">Lorem Ipsum has been the industry's standard dummy text ever since.</p>
  <div class="abs specs"><span><b>Bedrooms</b> : 3</span><span><b>Lot size</b> : 3</span><span><b>Bathrooms</b>: 3</span><span><b>Prperty type</b>: Single Family</span><span><b>Sqft</b>: 2.102</span><span><b>Year built</b>: 2010</span></div>
</div>
<div class="abs scroll"><div class="abs scroll-thumb"></div></div>

<div class="abs video">
  <div class="abs replay"><span></span>Replay</div>
  <div class="abs controls">
    <svg width="18" height="16" viewBox="0 0 18 16"><path d="M3 1 L16 8 L3 15 Z" fill="#bbb"/></svg>
    <svg width="18" height="16" viewBox="0 0 18 16"><path d="M1 5h4l5-4v14l-5-4H1z" fill="#bbb"/></svg>
    <span>3:45 / 3:45</span>
    <div class="progress"></div>
  </div>
</div>

<div class="abs investors">Investors! Learn About us <div class="doc"></div><small>[1.1mb - 16pgs]</small></div>

<div class="abs rule" style="left:28px;top:1145px;width:844px;background:#999"></div>
<p class="abs footer-links">Home | Our Story | Tenant | Owner | Contact us</p>
<p class="abs copyright">2011 © copyrights.quickhousebarnowl.received</p>
</body>
</html>
```